Dietitian needs awesome business card

I need a contemporary design that's eye catching but professional.
My card is to given to doctors, specialists and patients alike.
I manage patients with chronic diseases
I have uploaded my logo and current business card, I would also like the other Certified Clinical Nutritionist logo incorporated into the design

Target Market(s)

Doctors, specialists and patients

Industry/Entity Type

Healthcare

Contact Information for Business Card

www.brightfieldnutrition.com.au
Ph: 0427 561 903
Fax: 6457 2183
email: marcus.k.diet@fernmail.com
Space on the back of the card with: Appointment date, Appointment time and appointment location

Font styles to use
Serif

Colors
fbee3e
876aae
ffc214

Requirements
Must have
• My Logo
• Certified Clinical Nutritionist Logo
• My 4 locations - Pinebrook Medical Centre, North Corrin Health, Hollis Medical, Ashcombe Doctors Surgery
Nice to have
• I like the colours in my current business card

```html
<!DOCTYPE html>
<html lang="en">
<head>
<meta charset="utf-8">
<title>Brightfield Nutrition &amp; Dietetics – Business Card</title>
<link rel="stylesheet" href="https://fonts.googleapis.com/css2?family=Arimo:wght@400;700&display=swap">
<style>
  :root {
    --backdrop: #e9e5de;
    --card: #ffffff;
    --brand-blue: #1b7fc4;
    --brand-green: #8cc63f;
    --badge-orange: #f08a2a;
    --text-grey: #5a5a5a;
    --rule-grey: #9a9a9a;
  }
  * { box-sizing: border-box; margin: 0; padding: 0; }
  html, body { width: 1200px; height: 1023px; overflow: hidden; }
  body {
    background: var(--backdrop);
    font-family: "Arimo", Arial, sans-serif;
    position: relative;
  }
  .card {
    position: absolute;
    left: 260px;
    width: 680px;
    height: 388px;
    background: var(--card);
    box-shadow: 0 6px 18px rgba(0,0,0,0.18);
    overflow: hidden;
  }
  .card--front { top: 90px; }
  .card--back { top: 545px; }
  .card__band {
    position: absolute; left: 0; right: 0; bottom: 0;
    height: 22px;
    background: var(--brand-green);
    border-top: 4px solid var(--card);
    box-shadow: 0 -3px 0 var(--brand-blue);
  }

  /* front */
  .brand {
    position: absolute; left: 330px; top: 60px;
    display: flex; align-items: center; gap: 14px;
  }
  .brand__mark {
    width: 70px; height: 70px; border-radius: 50%;
    background: var(--brand-blue);
  }
  .brand__name {
    color: var(--brand-blue);
    font-size: 38px; font-weight: 400; line-height: 1;
  }
  .brand__tagline {
    color: var(--brand-blue);
    font-size: 17px; margin-top: 6px;
  }
  .credential {
    position: absolute; right: 36px; top: 196px;
    width: 118px; height: 82px;
    background: var(--badge-orange);
    display: flex; align-items: center; padding: 0 10px; gap: 8px;
  }
  .credential__seal {
    flex: none; width: 30px; height: 30px; border-radius: 50%;
    border: 2px solid #fff;
  }
  .credential__text {
    color: #fff; font-size: 10px; line-height: 1.25;
  }
  .person {
    position: absolute; left: 42px; top: 150px;
    color: var(--brand-blue);
    font-size: 30px; font-weight: 700; letter-spacing: 0.5px;
  }
  .contacts {
    position: absolute; left: 46px; top: 206px;
    list-style: none;
    color: var(--text-grey);
  }
  .contacts li {
    display: flex; align-items: center; gap: 12px;
    height: 25px; font-size: 17px;
  }
  .contacts li.contacts__strong { font-weight: 700; font-size: 19px; }
  .contacts svg { width: 16px; height: 16px; flex: none; }

  /* back */
  .appointment {
    position: absolute; left: 40px; top: 34px;
    color: var(--brand-blue);
    font-size: 30px; font-weight: 700; letter-spacing: 0.5px;
  }
  .slot {
    position: absolute; left: 40px; right: 40px;
    display: flex; align-items: flex-end; gap: 10px;
    color: var(--text-grey); font-size: 21px;
  }
  .slot--date { top: 96px; }
  .slot--time { top: 146px; }
  .slot__line { flex: 1; border-bottom: 2px dotted var(--rule-grey); height: 20px; }
  .location__label {
    position: absolute; left: 40px; top: 202px;
    color: var(--brand-green); font-size: 24px; font-weight: 700;
  }
  .locations {
    position: absolute; left: 40px; top: 244px; right: 40px;
    list-style: none;
    display: grid; grid-template-columns: 1fr 1fr; row-gap: 14px; column-gap: 20px;
  }
  .locations li {
    display: flex; align-items: center; gap: 12px;
    color: var(--brand-blue); font-size: 19px;
  }
  .locations__box {
    width: 18px; height: 18px; border: 1.5px solid var(--text-grey); flex: none;
  }
</style>
</head>
<body>

<section class="card card--front" aria-label="Business card front">
  <div class="brand">
    <span class="brand__mark"></span>
    <div>
      <div class="brand__name">Brightfield</div>
      <div class="brand__tagline">Nutrition &amp; Dietetics</div>
    </div>
  </div>

  <div class="credential" aria-label="Certified Clinical Nutritionist">
    <span class="credential__seal"></span>
    <span class="credential__text">Certified<br>Clinical<br>Nutritionist</span>
  </div>

  <h1 class="person">MARCUS KELLAWAY</h1>

  <ul class="contacts">
    <li class="contacts__strong">
      <svg viewBox="0 0 16 16"><rect x="2" y="6" width="12" height="8" rx="1" fill="none" stroke="#1b7fc4" stroke-width="1.5"/><rect x="4" y="2" width="8" height="5" fill="none" stroke="#1b7fc4" stroke-width="1.5"/></svg>
      6457 2183
    </li>
    <li class="contacts__strong">
      <svg viewBox="0 0 16 16"><path d="M4 2c1 0 2 3 2 4s-1 1-1 2 2 3 3 3 1-1 2-1 4 1 4 2-2 3-3 3C6 15 1 10 1 5c0-1 2-3 3-3z" fill="#1b7fc4"/></svg>
      0427 561 903
    </li>
    <li>
      <svg viewBox="0 0 16 16"><rect x="1" y="3" width="14" height="10" rx="1" fill="#1b7fc4"/><path d="M1 4l7 5 7-5" fill="none" stroke="#fff" stroke-width="1.3"/></svg>
      marcus.k.diet@fernmail.com
    </li>
    <li>
      <svg viewBox="0 0 16 16"><circle cx="8" cy="8" r="6.5" fill="none" stroke="#1b7fc4" stroke-width="1.5"/><path d="M1.5 8h13M8 1.5c3 3 3 10 0 13M8 1.5c-3 3-3 10 0 13" fill="none" stroke="#1b7fc4" stroke-width="1.2"/></svg>
      www.brightfieldnutrition.com.au
    </li>
  </ul>

  <div class="card__band"></div>
</section>

<section class="card card--back" aria-label="Business card back">
  <h2 class="appointment">APPOINTMENT</h2>
  <div class="slot slot--date"><span>Date:</span><span class="slot__line"></span></div>
  <div class="slot slot--time"><span>Time:</span><span class="slot__line"></span></div>

  <div class="location__label">Location :</div>
  <ul class="locations">
    <li><span class="locations__box"></span>Pinebrook Medical Centre</li>
    <li><span class="locations__box"></span>North Corrin Health</li>
    <li><span class="locations__box"></span>Ashcombe Doctors Surgery</li>
    <li><span class="locations__box"></span>Hollis Medical</li>
  </ul>

  <div class="card__band"></div>
</section>

</body>
</html>
```